New Innovative Counselling and psychotherapy Service needs Business Card design

Keep it simple and professional. On one side, just company name and logo (perhaps in all blue) and maybe a tag line.

On other side (all white) my name and Qualifications in centre

Industry/Entity Type

Health And Wellness

Contact Information for Business Card

Dara Whelby
Counsellor & Psychotherapist
BSc (Psychol.), BA, Dip. (Couns. & Psych.), PG.Cert (CBT), FGTrK, ONRE

I will also require Mobile no, Email and web site address of which I'll pass on to final designer.

Font styles to use
Sans Serif

Requirements
Must have
• My Logo Only and please use the colours in logo that is in it.
Should not have
• Any other images

```html
<!DOCTYPE html>
<html lang="en">
<head>
<meta charset="utf-8">
<title>ThriveLane Business Card</title>
<link rel="stylesheet" href="https://fonts.googleapis.com/css2?family=Work+Sans:wght@300;400;500;700&display=swap">
<style>
  :root {
    --stage: #1b1b1d;
    --card-white: #ffffff;
    --brand-blue: #4fb0e2;
    --brand-blue-deep: #3f9fd3;
    --brand-green: #8cc84b;
    --ink: #2b2b2b;
    --ink-soft: #5a5a5a;
    --back-text: #e4eef4;
  }
  * { box-sizing: border-box; margin: 0; padding: 0; }
  html, body {
    width: 1200px; height: 963px; overflow: hidden;
    background: var(--stage);
    font-family: "Work Sans", Arial, sans-serif;
  }
  .canvas { position: relative; width: 1200px; height: 963px; }
  .card {
    position: absolute; left: 250px; width: 700px; height: 400px;
    border-radius: 22px; overflow: hidden;
  }
  .card-front { top: 56px; background: linear-gradient(135deg, #f4f4f4 0%, var(--card-white) 45%); }
  .card-back { top: 507px; background: linear-gradient(135deg, #5ab6e6 0%, var(--brand-blue-deep) 100%); }

  .brand { position: absolute; left: 40px; top: 36px; display: flex; align-items: center; gap: 12px; }
  .brand-dot { width: 34px; height: 34px; border-radius: 50%; background: var(--brand-blue); }
  .brand-name { font-size: 30px; font-weight: 300; color: var(--ink-soft); letter-spacing: 0.5px; }

  .holder { position: absolute; right: 42px; top: 108px; text-align: right; }
  .holder-name { font-size: 34px; font-weight: 700; color: var(--brand-blue); letter-spacing: 1px; text-transform: uppercase; line-height: 1.1; }
  .holder-role { font-size: 17px; color: var(--ink); margin-top: 6px; }
  .holder-quals { font-size: 15px; color: var(--ink); margin-top: 4px; line-height: 1.45; }

  .divider { position: absolute; left: 40px; right: 42px; top: 232px; height: 1.5px; background: var(--brand-green); }

  .contact { position: absolute; left: 40px; top: 246px; list-style: none; font-size: 15px; color: var(--ink); line-height: 1.6; }
  .contact li { display: flex; align-items: center; gap: 9px; }
  .contact svg { width: 12px; height: 12px; flex: none; }
  .contact .web-accent { color: var(--brand-blue); }

  .wave { position: absolute; left: 0; bottom: 0; width: 700px; height: 100px; }

  .back-brand { position: absolute; inset: 0; display: flex; flex-direction: column; align-items: center; justify-content: center; gap: 18px; }
  .back-mark { display: flex; align-items: center; gap: 18px; }
  .back-dot { width: 70px; height: 70px; border-radius: 50%; background: var(--back-text); }
  .back-name { font-size: 56px; font-weight: 300; color: var(--back-text); }
  .back-web { position: absolute; bottom: 40px; width: 100%; text-align: center; font-size: 18px; color: var(--back-text); letter-spacing: 0.5px; }
</style>
</head>
<body>
<main class="canvas">
  <section class="card card-front">
    <div class="brand">
      <span class="brand-dot"></span>
      <span class="brand-name">ThriveLane</span>
    </div>

    <div class="holder">
      <h1 class="holder-name">Dara Whelby</h1>
      <p class="holder-role">Counsellor &amp; Psychotherapist</p>
      <p class="holder-quals">BSc (Psychol.), BA, Dip. (Couns. &amp; Psych.), PG.Cert<br>(CBT), FGTrK, ONRE</p>
    </div>

    <div class="divider"></div>

    <ul class="contact">
      <li><svg viewBox="0 0 12 12" fill="#4fb0e2"><path d="M3 0.5l2 2.5-1.2 1.3c.6 1.5 1.6 2.6 3 3.3L8 6.3l2.8 1.8-.9 2.6C5 10.5 1.2 6.6 1 1.6z"/></svg><span>888-410-2765</span></li>
      <li><svg viewBox="0 0 12 12"><path d="M0.6 2.2h10.8v7.6H0.6z M1.5 3l4.5 3.5L10.5 3" fill="none" stroke="#4fb0e2" stroke-width="1.2"/></svg><span>info@thrivelane.com</span></li>
      <li><svg viewBox="0 0 12 12" fill="none" stroke="#4fb0e2" stroke-width="1.1"><circle cx="6" cy="6" r="5.2"/><path d="M0.8 6h10.4M6 0.8c-2.4 2.8-2.4 7.6 0 10.4M6 0.8c2.4 2.8 2.4 7.6 0 10.4"/></svg><span>www.<span class="web-accent">thrivelane</span>.com</span></li>
    </ul>

    <svg class="wave" viewBox="0 0 700 100" preserveAspectRatio="none" aria-hidden="true">
      <path d="M0 42 C 200 78, 480 50, 700 100 L0 100 Z" fill="#4fb0e2"/>
      <path d="M0 42 C 200 78, 480 50, 700 100" fill="none" stroke="#8cc84b" stroke-width="5"/>
      <path d="M0 36 C 200 72, 480 44, 700 94" fill="none" stroke="#ffffff" stroke-width="5"/>
    </svg>
  </section>

  <section class="card card-back">
    <div class="back-brand">
      <div class="back-mark">
        <span class="back-dot"></span>
        <span class="back-name">ThriveLane</span>
      </div>
    </div>
    <p class="back-web">www.thrivelane.com</p>
  </section>
</main>
</body>
</html>
```